Halt and Thicken Hair Product Labels

We need a new label designed for a hair growth product. We are a US company that has created a revolutionary new cure for hereditary hair loss based on precision medicine.

Our new product is very different to all other hair loss products on the market in that it actually really works. Unfortunately there is no requirement in the US for truth in advertising by products that are not regulated by the FDA. We use only FDA approved active ingredients.

We want a fresh, new design to reflect this exciting product but also to demonstrate that it is medicine and it is regulated and not a fake product trying to scam people.

The Halt and tHicken topical hair solution is suspended in a ground-breaking foam or serum water based solution that does not cause scalp irritation and takes just seconds to apply each night before bed.

We would like to see a design that is modern, simple and bold, and includes our corporate colors in particular the green.

Brand colors: white, green #4ca26f, light blue #46b1d7, light grey #999999, dark grey #262626
See our website for more details: http://www.haltandthicken-example.com/

The final design should communicate health and well-being.

Note we had a previous set of labels which I have uploaded for reference, but these were based on our old logo. We have since created a new logo and so now need updated logos to reflect the new logo, colors and branding.

There are 2 product types for this label – Topical Solution and Pills each with different sizes.
Similar label design for both product variations. Just adjust sizing and some of the content.

Dimensions for labels:
1. Topical solution (2 variations) - 4 inches width (wraps the bottle to provide a front and back side) x 2 inches H
2. Pills (2 variations) – 3.5 inches width (also wraps) x 2 inches width

Attached:
Company name and logo to go onto label
I also attached examples of the old label based on our old logo. Not because you should follow that but just for background.
We are not open to an update of the logo or colors as part of the project.

Information to go on label:
See below for detailed for each label.

Target Market
Males between 20-45 years.

Health and well-being, modern, organic, forward thinking look And feel
Modern, Professional, Upmarket, Bold, Serious, New Generation, Precision Medicine.
We have a lot of male customers who are scared of medicines and chemicals so we don’t want the brand to look like it includes harsh chemicals or anything like that. We compound so we don’t have to include any preservatives etc in our products.

Label 1 - Hair Topical – Foam variation
2 inches tall x 4 inches wide

Front (information to be included):
Logo: Halt and Thicken (you cannot change the layout of the logo)
Personalized Topical Hair Solution
FDA Approved Ingredients in Proprietary Activation Base
Proprietary Compounded Formula Based on Your DNA

Back (information to be included):
Directions
Activate Solution Prior To Each Use By Shaking well
Apply Up to One Pump Nightly Before Bed
Each Bottle To Last 3 Months

Please call (555) 384-2916 for Refills

Important
This medicine has been created by Gerald Pumphrey MD following the Halt and Thicken personalized program to Stop your hair loss and Regrow your own hair. The formula is personalized just for you based on your cause of hair loss, DNA and personal biology.
Do Not Share with others as each person’s hair loss, biology and DNA are different.

Label 2 - Hair Topical – Serum variation
2 inches tall x 3.5 inches wide

Logo: Halt and Thicken

Directions
Apply Up to Seven (7) Drops Nightly Before Bed To Affected Areas of the Scalp (also want a variation that says: Apply Up to Eleven (11) Drops...)

Important

Label 3 - Dutasteride Capsules

Information to be included:
Logo: Halt and Thicken
Compounded Dutasteride to Block Circulating DHT
Personalized Hair Dose Based on Your DNA 0.7mg
Take 1 x Capsule Daily

Label 4 - Folvex Capsules

Logo: Halt and Thicken
Other verbiage to be included:
Compounded Dutasteride to Block Circulating DHT Plus Anastrazole to Block Conversion to Estrogen
Personalized Dose Based on Your DNA: DT 0.7mg + AZ 0.2mg
Take 1 x Capsule Daily
Updates

Hello designers! I have extended the timeline for this project because we are looking for new different designs to the ones we had previously. This was not a project to simply replace the logo and have the same layout and design, I included the previous design for reference of the information included not for design/style. It was made to suit the old logo. Now we have a new logo we need a new completely different design to match that logo. If you are interested in participating in this contest it would be great if you could please submit new and original design ideas for me to select from. I will not select a design that is the same as the previous one. Thanks so much! Marnie

Target Market(s)

Males 20 to 45

Industry/Entity Type

Health And Wellness

Font styles to use
Sans Serif

Colors
00a990
ffffff
333333
cfcfcf

Requirements
Must have
• Must use our logo and brand colors
Should not have
• Don't use any red except for warnings

```html
<!DOCTYPE html>
<html lang="en">
<head>
<meta charset="utf-8">
<title>Halt and Thicken – Label Set</title>
<link rel="stylesheet" href="https://fonts.googleapis.com/css2?family=Oswald:wght@300;400;500&family=Pathway+Gothic+One&family=Roboto:wght@400;500&display=swap">
<style>
  :root{
    --bg:#cfcfcf;
    --slate:#58585a;
    --slate-light:#6e6e70;
    --green:#4aa26b;
    --white:#ffffff;
    --grey:#9a9a9a;
    --logo-grey:#8d8d8d;
    --capsule-light:#cfcfcf;
  }
  *{box-sizing:border-box;margin:0;padding:0}
  html,body{width:1200px;height:686px;overflow:hidden;background:var(--bg)}
  .stage{position:absolute;left:0;top:0;width:1500px;height:858px;transform:scale(.8);transform-origin:0 0}
  .label{position:absolute;height:316px;overflow:hidden;color:var(--white);font-family:"Pathway Gothic One",sans-serif}
  .label--topical{width:631px}
  .label--oral{width:555px}
  .label--slate{background:var(--slate)}
  .label--green{background:var(--green)}

  .logo-tab{position:absolute;left:0;top:0;background:var(--white);display:flex;align-items:center;gap:12px;padding-left:44px}
  .label--topical .logo-tab{width:263px;height:108px;border-bottom-right-radius:40px}
  .label--oral .logo-tab{width:232px;height:102px;border-radius:0 60px 60px 0;padding-left:24px}
  .logo-dot{width:26px;height:26px;border-radius:50%;background:var(--green);flex:none}
  .logo-name{font-family:"Oswald",sans-serif;font-weight:400;font-size:22px;color:var(--logo-grey);text-transform:uppercase;white-space:nowrap}

  .size-tag{position:absolute;left:48px;top:128px;width:37px;height:147px;background:var(--white)}
  .size-tag__word{position:absolute;left:0;top:0;width:37px;height:112px;writing-mode:vertical-rl;transform:rotate(180deg);display:flex;align-items:center;justify-content:center;font-family:"Oswald",sans-serif;font-weight:300;font-size:19px;letter-spacing:1px;color:var(--slate)}
  .label--green .size-tag{background:var(--slate)}
  .label--green .size-tag__word{color:var(--white)}
  .size-tag__vol{position:absolute;left:0;bottom:0;width:37px;height:35px;background:var(--grey);font-size:18px;display:flex;align-items:center;justify-content:center;color:var(--white)}
  .label--slate .size-tag__vol{background:var(--slate-light)}

  .headline{position:absolute;left:97px;top:122px;font-family:"Oswald",sans-serif;font-weight:400;font-size:50px;line-height:1;transform:scaleX(.78);transform-origin:0 0;white-space:nowrap;letter-spacing:-1px}
  .hero{position:absolute;left:95px;top:160px;font-family:"Oswald",sans-serif;font-weight:400;font-size:128px;line-height:1;transform-origin:0 0;white-space:nowrap;letter-spacing:-3px}
  .hero--serum{transform:scaleX(.52)}
  .hero--foam{transform:scaleX(.66)}
  .hero--grey{color:var(--grey)}
  .tagline{position:absolute;left:48px;top:281px;font-size:16px;white-space:nowrap;transform:scaleX(.86);transform-origin:0 0}

  .strip{position:absolute;top:0;height:316px;width:35px}
  .label--topical .strip{left:300px}
  .label--oral .strip{left:258px;width:33px}
  .label--slate .strip{background:var(--green)}
  .label--green .strip{background:var(--slate)}
  .strip__text{position:absolute;left:0;width:100%;writing-mode:vertical-rl;transform:rotate(180deg);display:flex;flex-direction:column;justify-content:flex-start;align-items:center;font-family:"Oswald",sans-serif;font-weight:500;font-size:11.5px;line-height:1.1;text-transform:uppercase;white-space:nowrap}
  .label--topical .strip__text{top:66px;height:190px}
  .label--oral .strip__text{top:50px;height:196px}
  .strip__badge{position:absolute;left:7px;bottom:18px;width:20px;height:38px;background:var(--white);border-radius:2px}

  .info{position:absolute;top:0;height:316px;padding-top:16px;width:262px}
  .label--topical .info{left:360px}
  .label--oral .info{left:301px}
  .info h3{font-weight:400;font-size:15px;line-height:18px;text-transform:uppercase}
  .info ul{list-style:none;margin-top:4px}
  .info li{font-size:12.5px;line-height:16px;white-space:nowrap}
  .info li::before{content:"• "}
  .rule{border-top:1px solid rgba(255,255,255,.85);margin:6px 0}
  .info .last,.info .refill{white-space:nowrap;transform-origin:0 50%;line-height:28px}
  .info .last{font-size:20px;transform:scaleX(.8)}
  .info .refill{font-size:24px;transform:scaleX(.76)}
  .info .dose{font-size:14px;line-height:16px;margin-bottom:14px;white-space:nowrap}
  .info .direction{font-size:15px;line-height:20px}
  .info .important{font-size:13px;line-height:16px;white-space:nowrap}

  .notice{position:absolute;bottom:0;background:var(--white);border-top-left-radius:20px;border-top-right-radius:6px;color:var(--green);text-align:center;font-size:15px;line-height:17px;white-space:nowrap;display:flex;align-items:center;justify-content:center}
  .label--topical .notice{left:362px;width:240px;height:48px}
  .label--oral .notice{left:303px;width:233px;height:48px}
  .label--green .notice{color:var(--slate)}
  .notice--open{background:transparent}
  .label--green .notice--open{color:var(--white)}

  .oral-name{position:absolute;left:18px;top:120px;font-family:"Oswald",sans-serif;font-weight:400;font-size:38px;line-height:1;transform:scaleX(.72);transform-origin:0 0;white-space:nowrap}
  .oral-hero{position:absolute;left:18px;top:150px;font-family:"Oswald",sans-serif;font-weight:400;font-size:92px;line-height:1;transform:scaleX(.68);transform-origin:0 0;white-space:nowrap;letter-spacing:-2px}
  .oral-sub{position:absolute;left:18px;top:244px;font-size:15px;line-height:18px;white-space:nowrap;transform:scaleX(.92);transform-origin:0 0}
  .count{position:absolute;left:20px;bottom:12px;font-family:"Roboto",sans-serif;font-size:17px;letter-spacing:.5px}
  .icon{position:absolute}
</style>
</head>
<body>
<main class="stage">

  <section class="label label--topical label--slate" style="left:123px;top:80px">
    <div class="logo-tab"><span class="logo-dot"></span><span class="logo-name">Halt and Thicken</span></div>
    <div class="size-tag"><span class="size-tag__word">PERSONALIZED</span><span class="size-tag__vol">50 mL</span></div>
    <div class="headline">HAIR TOPICAL</div>
    <div class="hero hero--serum hero--grey">SERUM</div>
    <div class="tagline">Proprietary Compounded Formula Based on Your DNA</div>
    <div class="strip"><div class="strip__text"><span>Active Ingredients in Proprietary</span><span>Activation Base</span></div><span class="strip__badge"></span></div>
    <div class="info">
      <h3>Directions</h3>
      <ul><li>Apply Up to Eleven Drops Nightly Before Bed To<br>&nbsp;&nbsp;Affected Areas of the Scalp.</li></ul>
      <div class="rule"></div>
      <p class="last">Each Bottle To Last 3 Months</p>
      <p class="refill">Please call (555) 384-2916 for Refills</p>
      <div class="rule"></div>
      <h3>Important</h3>
      <p class="important">This medicine has been created by Gerald Pumphrey MD<br>following the Halt and tHicken personalized program<br>to Stop your hair loss and reGrow your own hair. The<br>formula is personalized just for you based on your<br>cause of hair loss, DNA and personal biology.</p>
    </div>
    <div class="notice">Do Not Share with others as each person's hair loss,<br>biology and DNA are different.</div>
  </section>

  <section class="label label--oral label--slate" style="left:822px;top:79px">
    <div class="logo-tab"><span class="logo-dot"></span><span class="logo-name">Halt and Thicken</span></div>
    <div class="oral-name">DUTASTERIDE</div>
    <div class="oral-hero hero--grey">PILLS</div>
    <svg class="icon" style="left:148px;top:160px" width="30" height="76" viewBox="0 0 30 76" aria-hidden="true">
      <path d="M0 15a15 15 0 0 1 30 0v23H0z" fill="#fff"/><path d="M0 40h30v21a15 15 0 0 1-30 0z" fill="#4aa26b"/>
    </svg>
    <div class="oral-sub">Compounded Dutasteride to Block Circulating DHT</div>
    <div class="count">90 PILLS</div>
    <div class="strip"><div class="strip__text"><span>Only the actives - compounded</span><span>FDA approved active ingredients</span></div><span class="strip__badge"></span></div>
    <div class="info">
      <p class="dose">Personalized Hair Dose<br>Based on Your DNA: 0.5mg</p>
      <h3>Directions</h3>
      <p class="direction">Take 1 x Pill Daily With Protein.</p>
      <div class="rule"></div>
      <p class="refill">Please call (555) 384-2916 for Refills</p>
      <div class="rule"></div>
      <h3>Important</h3>
      <p class="important">This medicine has been created by Gerald Pumphrey MD<br>following the Halt and tHicken personalized program<br>to Stop your hair loss and reGrow your own hair. The<br>formula is personalized just for you based on your<br>cause of hair loss, DNA and personal biology.</p>
    </div>
    <div class="notice">Do Not Share with others as each person's hair loss,<br>biology and DNA are different.</div>
  </section>

  <section class="label label--topical label--green" style="left:123px;top:462px">
    <div class="logo-tab"><span class="logo-dot"></span><span class="logo-name">Halt and Thicken</span></div>
    <div class="size-tag"><span class="size-tag__word">PERSONALIZED</span><span class="size-tag__vol">50 mL</span></div>
    <div class="headline">HAIR TOPICAL</div>
    <div class="hero hero--foam">FOAM</div>
    <div class="tagline">Proprietary Compounded Formula Based on Your DNA</div>
    <div class="strip"><div class="strip__text"><span>Active Ingredients in Proprietary</span><span>Activation Base</span></div><span class="strip__badge"></span></div>
    <div class="info">
      <h3>Directions</h3>
      <ul><li>Activate Solution Prior To Each Use By Shaking well.</li><li>Apply Up to One Pump Nightly Before Bed.</li></ul>
      <div class="rule"></div>
      <p class="last">Each Bottle To Last 3 Months</p>
      <p class="refill">Please call (555) 384-2916 for Refills</p>
      <div class="rule"></div>
      <h3>Important</h3>
      <p class="important">This medicine has been created by Gerald Pumphrey MD<br>following the Halt and tHicken personalized program<br>to Stop your hair loss and reGrow your own hair. The<br>formula is personalized just for you based on your<br>cause of hair loss, DNA and personal biology.</p>
    </div>
    <div class="notice">Do Not Share with others as each person's hair loss,<br>biology and DNA are different.</div>
  </section>

  <section class="label label--oral label--green" style="left:822px;top:462px">
    <div class="logo-tab"><span class="logo-dot"></span><span class="logo-name">Halt and Thicken</span></div>
    <div class="oral-name">FOLVEX</div>
    <svg class="icon" style="left:94px;top:126px" width="80" height="30" viewBox="0 0 80 30" aria-hidden="true">
      <path d="M15 0h24v30H15a15 15 0 0 1 0-30z" fill="#cfcfcf"/><path d="M41 0h24a15 15 0 0 1 0 30H41z" fill="#58585a"/>
    </svg>
    <div class="oral-hero">CAPSULE</div>
    <div class="oral-sub">Compounded Dutasteride to Block Circulating DHT<br>Plus Anastrazole to Block Conversion to Estrogen</div>
    <div class="count">90 CAPSULES</div>
    <div class="strip"><div class="strip__text"><span>Only the actives - compounded</span><span>FDA approved active ingredients</span></div><span class="strip__badge"></span></div>
    <div class="info">
      <p class="dose">Personalized Dose Based on Your<br>DNA: DT 0.7mg + AZ 0.2mg</p>
      <h3>Directions</h3>
      <p class="direction">Take 1 x Capsule Daily</p>
      <div class="rule"></div>
      <p class="refill">Please call (555) 384-2916 for Refills</p>
      <div class="rule"></div>
      <h3>Important</h3>
      <p class="important">This medicine has been created by Gerald Pumphrey MD<br>following the Halt and tHicken personalized program<br>to Stop your hair loss and reGrow your own hair. The<br>formula is personalized just for you based on your<br>cause of hair loss, DNA and personal biology.</p>
    </div>
    <div class="notice notice--open">Do Not Share with others as each person's hair loss,<br>biology and DNA are different.</div>
  </section>

</main>
</body>
</html>
```